Etikett für Rotweinflasche
Liebe farbkosmos Atelier, wir werden uns bei der endgültigen Etikettengestaltung (finale Größe + Rückseite) noch an Euch melden. Bitte sendet uns euren Kontakt an helga.brandt@morvelli.wine
Zielgruppe
Morvelli Italia ist ein exklusives Boutique-Weingut in Sizilien, das hochqualitative Spitzenweine in kleinen Mengen mit modernster Technologie und stets nachhaltig erzeugt. Wir hinterfragen sowohl in der Agronomie im Weingarten als auch in der Önologie im Weinkeller alle herrschenden Traditionen und trachten danach, stets das beste Endprodukt zu kreieren. Der vulkanische, kalkreiche Boden Siziliens sowie trockene, sonnenreiche und niederschlagsarme Vegetationsperioden sind unsere optimale Basis.
Zielgruppe: Internationale Genussmenschen jeglichen Alters, die sich bewusst auch höherpreisige Weine (um die €30+) gönnen , vor allem kunstaffine young professionals mit Qualitäts-& Nachhaltigkeitsanspruch
Aufgabenstellung
Das Etikett ist für Rotwein-Flaschen (Cabernet Sauvignon / Nero D'Avola / Frappato / Syrah / Cerasuolo / Petit Verdot / sowie einen Bourdeaux-Cuveè aus Cabernet Sauvignon und Petit Verdot) .
Die Flasche ist reinschwarz, sehr hochwertig und schwer.
Flaschenform: Bordeauxflasche siehe technisches Datenblatt
Sleeve über dem Korken: schwarz mit weißer Schrift wie bisher
Zu gestalten ist das Etikett der Vorderseite. Zumindest die jeweilige Rotwein-Sorte ist auch textlich darzustellen (zwecks Scannen mit Trubel-App)
Der Kreativität kann freien Lauf gelassen werden! Unterscheidbarkeit vom Markt ist explizit gewollt.
Unsere aktuellen Etiketten und Markenauftritt siehe: https://morvelli.wine/shop/

```html
<!DOCTYPE html>
<html lang="de">
<head>
<meta charset="utf-8">
<title>Morvelli Italia – Etikettenserie Rotwein</title>
<link href="https://fonts.googleapis.com/css2?family=Playfair+Display:wght@400&display=swap" rel="stylesheet">
<style>
  :root {
    --page: #f4f4f4;
    --ink: #fbf3f1;
    --wine-deep: #2a0610;
    --wine: #6e1224;
    --berry: #b3224f;
    --rose: #d14a7c;
    --ember: #e8502a;
    --night: #0b0a12;
    --plum: #3a1236;
  }
  * { box-sizing: border-box; margin: 0; padding: 0; }
  html, body { width: 1200px; height: 1200px; overflow: hidden; background: var(--page); }
  .series { position: relative; width: 1200px; height: 1200px; }
  .label {
    position: absolute; width: 241px; height: 519px; overflow: hidden;
    box-shadow: 0 4px 10px rgba(0,0,0,.18);
    font-family: "Playfair Display", Georgia, serif; color: var(--ink); text-align: center;
  }
  .label__art { position: absolute; inset: 0; }
  .brand { position: absolute; top: 78px; left: 0; right: 0; line-height: 1; font-weight: 400; }
  .brand__name { display: block; font-size: 17px; letter-spacing: .04em; }
  .brand__place { display: block; font-size: 11px; letter-spacing: .08em; margin-top: 3px; }
  .variety { position: absolute; top: 244px; left: 0; right: 0; font-size: 17px; letter-spacing: .32em; line-height: 25px; padding-left: .32em; font-weight: 400; }
  .blend { position: absolute; bottom: 34px; left: 0; right: 0; font-size: 10px; letter-spacing: .3em; line-height: 17px; padding-left: .3em; }

  .col-1 { left: 40px; } .col-2 { left: 333px; } .col-3 { left: 626px; } .col-4 { left: 918px; }
  .row-1 { top: 60px; } .row-2 { top: 620px; }

  .art-cabernet { background:
    radial-gradient(ellipse 40% 70% at 20% 30%, rgba(209,74,124,.9), transparent 70%),
    radial-gradient(ellipse 30% 60% at 45% 75%, rgba(179,34,79,.8), transparent 70%),
    linear-gradient(90deg, var(--wine) 0%, var(--berry) 40%, var(--wine-deep) 80%, var(--night) 100%); }
  .art-cerasuolo { background:
    radial-gradient(ellipse 60% 18% at 55% 45%, rgba(232,80,42,.85), transparent 70%),
    radial-gradient(ellipse 50% 20% at 60% 25%, rgba(200,60,50,.6), transparent 70%),
    radial-gradient(ellipse 30% 15% at 75% 90%, rgba(232,80,42,.7), transparent 70%),
    linear-gradient(160deg, #1a140e, #2a0c0a 50%, #18160f); }
  .art-syrah { background:
    linear-gradient(125deg, var(--wine) 0%, var(--berry) 35%, #c9365c 45%, var(--wine) 55%, var(--wine-deep) 100%); }
  .art-frappato { background:
    radial-gradient(ellipse 40% 60% at 50% 45%, rgba(190,40,60,.8), transparent 70%),
    linear-gradient(90deg, #200608, var(--wine) 35%, #9a1c30 55%, var(--wine) 75%, #150506); }
  .art-bordeaux-pv { background:
    radial-gradient(ellipse 50% 45% at 80% 45%, rgba(140,25,45,.85), transparent 70%),
    linear-gradient(90deg, #050406 0%, #100508 35%, #4a0c18 100%); }
  .art-bordeaux-cs { background:
    radial-gradient(ellipse 55% 18% at 50% 22%, rgba(220,100,130,.75), transparent 70%),
    radial-gradient(ellipse 30% 20% at 45% 75%, rgba(140,30,70,.6), transparent 70%),
    linear-gradient(180deg, #250a14, var(--wine) 50%, #3a060c); }
  .art-petit { background:
    radial-gradient(ellipse 40% 35% at 30% 40%, rgba(160,30,50,.6), transparent 70%),
    radial-gradient(ellipse 40% 30% at 55% 70%, rgba(110,30,90,.6), transparent 70%),
    linear-gradient(180deg, #120a18, var(--plum) 60%, #12081a); }
  .art-nero { background:
    radial-gradient(ellipse 20% 70% at 95% 70%, rgba(240,90,30,.9), transparent 70%),
    radial-gradient(ellipse 60% 50% at 40% 60%, rgba(140,25,25,.6), transparent 70%),
    linear-gradient(160deg, #1a0507, #3a0a0a 60%, #240606); }
</style>
</head>
<body>
<main class="series">
  <article class="label col-1 row-1">
    <div class="label__art art-cabernet" role="img" aria-label="Abstrakte Fotografie fließender Seide in Magenta und Weinrot"></div>
    <div class="brand"><span class="brand__name">MORVELLI</span><span class="brand__place">ITALIA</span></div>
    <h2 class="variety">CABERNET<br>SAUVIGNON</h2>
  </article>
  <article class="label col-2 row-1">
    <div class="label__art art-cerasuolo" role="img" aria-label="Bewegungsunschärfe in Orangerot auf dunklem Grund"></div>
    <div class="brand"><span class="brand__name">MORVELLI</span><span class="brand__place">ITALIA</span></div>
    <h2 class="variety" style="top:256px">CERASUOLO</h2>
  </article>
  <article class="label col-3 row-1">
    <div class="label__art art-syrah" role="img" aria-label="Diagonale Stoffbahn in Himbeerrot"></div>
    <div class="brand"><span class="brand__name">MORVELLI</span><span class="brand__place">ITALIA</span></div>
    <h2 class="variety" style="top:256px">SYRAH</h2>
  </article>
  <article class="label col-4 row-1">
    <div class="label__art art-frappato" role="img" aria-label="Senkrecht fallender roter Vorhang, weich verwischt"></div>
    <div class="brand"><span class="brand__name">MORVELLI</span><span class="brand__place">ITALIA</span></div>
    <h2 class="variety" style="top:256px">FRAPPATO</h2>
  </article>

  <article class="label col-1 row-2">
    <div class="label__art art-bordeaux-pv" role="img" aria-label="Dunkle Schwarz-Rot-Abstraktion mit weichen Falten"></div>
    <div class="brand"><span class="brand__name">MORVELLI</span><span class="brand__place">ITALIA</span></div>
    <h2 class="variety">BORDEAUX<br>CUVEÈ</h2>
    <p class="blend">PETIT VERDOT</p>
  </article>
  <article class="label col-2 row-2">
    <div class="label__art art-bordeaux-cs" role="img" aria-label="Rosafarbene Rauchschleier auf Weinrot"></div>
    <div class="brand"><span class="brand__name">MORVELLI</span><span class="brand__place">ITALIA</span></div>
    <h2 class="variety">BORDEAUX<br>CUVEÈ</h2>
    <p class="blend">CABERNET<br>SAUVIGNON</p>
  </article>
  <article class="label col-3 row-2">
    <div class="label__art art-petit" role="img" aria-label="Verschwommene Rot- und Violetttöne auf Nachtblau"></div>
    <div class="brand"><span class="brand__name">MORVELLI</span><span class="brand__place">ITALIA</span></div>
    <h2 class="variety">PETIT<br>VERDOT</h2>
  </article>
  <article class="label col-4 row-2">
    <div class="label__art art-nero" role="img" aria-label="Leuchtender orangefarbener Lichtbogen auf dunklem Rot"></div>
    <div class="brand"><span class="brand__name">MORVELLI</span><span class="brand__place">ITALIA</span></div>
    <h2 class="variety">NERO<br>D‘ AVOLA</h2>
  </article>
</main>
</body>
</html>
```